Popup Nightclub Grand Opening Flyer

We need to design a flyer for the grand opening of an upscale, exclusive nightclub called "Lantern". The design needs to be chic and exclusive. The background should be black and the text should primarily be white. We like minimalist designs.

Here is the text for the flyer
-
Velvetroll Atlanta Presents

Lantern (LOGO)

A Popup Nightclub Experience
For one night Only

Friday, October 18, 2013
Party begins at 9PM

INVITE ONLY

See invitation for location details
(Velvetroll Atlanta logo)

-
Examples we like

http://cdn4-x.pressfolio-example.com/sites/default/files/styles/image_content_width/hash/3b/fd/2468013579_4421_flyer.jpg?itok=K9rtQw2z

http://files.hubspace-example.net/files/8Hqq-Tr72WWE3kaRbTmcxP5QZK2F396J8nbRw4CKMHfdX2Y7qSEF-MqjxDoNrLY3QCyQJD7npjGaRq3k-Mhx6hqf3MDSWf8r3/2zenSaturdays.jpg

http://morvex-example.com/wp-content/uploads/siteskin/widgetkit/gallery/2zen/2zen-gen_qstay4-01.jpg

Hi All, one thing that we are seeing that we don't like is on over emphasis on the phrase "a popup nightclub experience" please don't make this the largest thing on the flyer

Target Market(s)

Target market is 25-35 year olds who are affluent (rich) and like luxury brands

Requirements
Must have
• Dark Background
Nice to have
• Velvetroll Logo on the bottom
Modern text that isn't curvy
Should not have
• Curved text

```html
<!DOCTYPE html>
<html lang="en">
<head>
<meta charset="utf-8">
<title>Lantern Popup Nightclub Flyer</title>
<link rel="stylesheet" href="https://fonts.googleapis.com/css2?family=Questrial&family=Roboto+Condensed:wght@300;400;700&display=swap">
<style>
  :root {
    --ink: #050505;
    --white: #f4f4f4;
    --silver-light: #f2f2f2;
    --silver-mid: #a9a9a9;
    --silver-dark: #6f6f6f;
    --rule: #9a9a9a;
    --dots: #d8d8d8;
    --muted: #d6d6d6;
  }
  html, body {
    margin: 0;
    padding: 0;
    width: 867px;
    height: 1200px;
    overflow: hidden;
    background: var(--ink);
  }
  .flyer {
    position: relative;
    width: 867px;
    height: 1200px;
    overflow: hidden;
    background: var(--ink);
    color: var(--white);
    font-family: "Questrial", sans-serif;
  }
  .backdrop { position: absolute; inset: 0; }
  .centered {
    position: absolute;
    left: 0;
    width: 100%;
    text-align: center;
    white-space: nowrap;
  }
  .presenter { top: 90px; font-size: 27px; letter-spacing: 0.5px; }
  .presents { top: 126px; font-size: 20px; letter-spacing: 7px; }
  .club-mark {
    position: absolute;
    left: 381px;
    top: 176px;
    width: 106px;
    height: 106px;
    border-radius: 50%;
    background: radial-gradient(circle at 40% 35%, var(--silver-light), var(--silver-mid) 60%, var(--silver-dark));
  }
  .club-name {
    top: 322px;
    font-size: 62px;
    line-height: 66px;
    letter-spacing: 10px;
    padding-left: 10px;
    box-sizing: border-box;
    color: var(--silver-light);
  }
  .club-type {
    top: 392px;
    font-size: 22px;
    letter-spacing: 4px;
    padding-left: 4px;
    box-sizing: border-box;
    color: var(--silver-light);
  }
  .rule {
    position: absolute;
    left: 293px;
    width: 282px;
    height: 2px;
    background: linear-gradient(90deg, transparent, var(--rule) 15%, #ffffff 50%, var(--rule) 85%, transparent);
  }
  .rule-top { top: 484px; }
  .rule-mid { top: 738px; }
  .rule-bottom { top: 806px; }
  .headline {
    top: 508px;
    margin: 0;
    font-family: "Roboto Condensed", sans-serif;
    font-weight: 700;
    font-size: 56px;
    line-height: 70px;
    text-transform: uppercase;
    background: linear-gradient(180deg, var(--silver-light) 10%, var(--silver-mid) 55%, var(--silver-light) 90%);
    -webkit-background-clip: text;
    background-clip: text;
    color: transparent;
  }
  .tagline { top: 752px; font-size: 33px; line-height: 40px; color: #e6e6e6; letter-spacing: 0.5px; }
  .date-block {
    position: absolute;
    left: 50%;
    top: 904px;
    transform: translateX(-50%);
    border-top: 2px dotted var(--dots);
    border-bottom: 2px dotted var(--dots);
    padding: 5px 4px 6px;
    text-align: center;
    white-space: nowrap;
    font-family: "Roboto Condensed", sans-serif;
  }
  .date { font-weight: 700; font-size: 28px; line-height: 32px; }
  .start { font-weight: 300; font-size: 28px; line-height: 32px; letter-spacing: 0.3px; }
  .access {
    top: 1000px;
    font-family: "Roboto Condensed", sans-serif;
    font-weight: 700;
    font-size: 18px;
    letter-spacing: 5px;
    padding-left: 5px;
    box-sizing: border-box;
  }
  .location-note { top: 1040px; font-size: 17px; letter-spacing: 1px; color: var(--muted); }
  .host {
    position: absolute;
    left: 0;
    width: 100%;
    top: 1086px;
    display: flex;
    justify-content: center;
    align-items: center;
    gap: 12px;
  }
  .host-square { width: 22px; height: 22px; background: var(--white); }
  .host-name { font-size: 25px; letter-spacing: 4px; color: var(--white); }
</style>
</head>
<body>
<main class="flyer">
  <svg class="backdrop" width="867" height="1200" viewBox="0 0 867 1200" aria-hidden="true">
    <defs>
      <radialGradient id="centreGlow" cx="433" cy="650" r="360" gradientUnits="userSpaceOnUse">
        <stop offset="0" stop-color="#3a3533"/>
        <stop offset="0.55" stop-color="#1d1a19"/>
        <stop offset="1" stop-color="#050505"/>
      </radialGradient>
      <radialGradient id="topGlow" cx="433" cy="-20" r="230" gradientUnits="userSpaceOnUse">
        <stop offset="0" stop-color="#2d2a28"/>
        <stop offset="1" stop-color="#050505" stop-opacity="0"/>
      </radialGradient>
      <radialGradient id="bottomGlow" cx="433" cy="1220" r="230" gradientUnits="userSpaceOnUse">
        <stop offset="0" stop-color="#2a2725"/>
        <stop offset="1" stop-color="#050505" stop-opacity="0"/>
      </radialGradient>
    </defs>
    <rect width="867" height="1200" fill="url(#centreGlow)"/>
    <path d="M0 0 H867 V420 Q433 500 0 420 Z" fill="#050505"/>
    <path d="M0 878 Q433 800 867 878 V1200 H0 Z" fill="#050505"/>
    <rect width="867" height="300" fill="url(#topGlow)"/>
    <rect y="900" width="867" height="300" fill="url(#bottomGlow)"/>
  </svg>

  <div class="centered presenter">Velvetroll Atlanta</div>
  <div class="centered presents">Presents</div>

  <div class="club-mark" aria-hidden="true"></div>
  <div class="centered club-name">LANTERN</div>
  <div class="centered club-type">NIGHTCLUB</div>

  <div class="rule rule-top"></div>
  <h1 class="centered headline">A Popup<br>Nightclub<br>Experience</h1>
  <div class="rule rule-mid"></div>
  <div class="centered tagline">For one night only</div>
  <div class="rule rule-bottom"></div>

  <div class="date-block">
    <div class="date">FRIDAY, OCTOBER 18, 2013</div>
    <div class="start">PARTY BEGINS AT 9PM</div>
  </div>

  <div class="centered access">INVITE ONLY</div>
  <div class="centered location-note">See invitation for location details</div>

  <div class="host">
    <span class="host-square" aria-hidden="true"></span>
    <span class="host-name">VELVETROLL ATLANTA</span>
  </div>
</main>
</body>
</html>
```